Upstart Retirement Planning Firm needs help with business card design

Harborview Nest Advisors, LLC is looking for help with business card design. We give advice on investments, insurance, and other financial matters related to retirement. There are some required disclosures that we will provide but mostly we are looking for a professional, classy business card that reflects the theme we have chosen. We have a logo that is attached but we would like to add a phrase; "Turning Your Earned Income Into Retirement Income"

Doubled sided only so that we can add the required disclosures (needed for our industry) on the back of the card. We will provide the exact words for this in 1-2 days.

Target Market(s)

Retirees and Pre-retirees. Professionals 50+ years old

Industry/Entity Type

Financial Planning

Contact Information for Business Card

We currently have two people who will need separate cards so we'd like to have a template so that we can add names for new cards in the future.

For the first run, please show the following information.

Gregor Pelham, MBA, ChFC®, CLU®
Financial Advisor, Registered Representative
gpelham@harborviewnest.example
Phone: (555) 318-2946
Toll Free Fax: (800) 555-0193

Address is
2187 Meadowlark Ridge Rd.
Suite K418
Virginia Beach, VA 23999

Colors
3277b5

Requirements
Must have
• Logo, contact info, small phase to describe business (in description), required legal disclosures on back of the card as follows (in small font)
• Gregor Pelham is a registered representative of and offers securities through Brightmoor Capital Brokerage Corporation, Member FNQX. Brightmoor Capital Brokerage Corporation is a member of the Brightmoor Capital Alliance which is the marketing name for Brightmoor Holding Corporation and its affiliates.
Nice to have
• Rounded edges, raised letters
Should not have
• any colors that aren't in the logo (other than black for font)

```html
<!DOCTYPE html>
<html lang="en">
<head>
<meta charset="utf-8">
<title>Harborview Nest Advisors — Business Card</title>
<link rel="stylesheet" href="https://fonts.googleapis.com/css2?family=Source+Sans+3:wght@400;600;700&display=swap">
<style>
  :root {
    --brand-blue: #2a5699;
    --ink-blue: #1f4b94;
    --text-grey: #808080;
    --card-white: #ffffff;
    --backdrop-top: #1d1d1d;
    --backdrop-bottom: #050505;
    --card-font: "Source Sans 3", "Helvetica Neue", Arial, sans-serif;
  }
  * { box-sizing: border-box; margin: 0; padding: 0; }
  html, body { width: 1200px; height: 900px; overflow: hidden; }
  body {
    position: relative;
    background: linear-gradient(180deg, var(--backdrop-top) 0%, #121212 60%, var(--backdrop-bottom) 100%);
    font-family: var(--card-font);
  }
  .card {
    position: absolute;
    top: 170px;
    width: 347px;
    height: 561px;
  }
  .card-front { left: 259px; background: var(--card-white); }
  .card-back { left: 631px; background: var(--brand-blue); }

  .accent-tab {
    position: absolute;
    left: 102px;
    width: 143px;
    background: var(--brand-blue);
  }
  .accent-tab-top { top: 0; height: 30px; }
  .accent-tab-bottom { bottom: 0; height: 28px; }

  .brand-name {
    position: absolute;
    left: 0; right: 0;
    text-align: center;
    font-weight: 600;
    letter-spacing: 0.04em;
  }
  .card-front .brand-name {
    top: 168px;
    color: var(--ink-blue);
    font-size: 18px;
    line-height: 1.25;
  }
  .brand-rule {
    position: absolute;
    top: 214px;
    left: 42px;
    width: 263px;
    height: 1px;
    background: var(--text-grey);
  }

  .contact {
    position: absolute;
    top: 248px;
    left: 0; right: 0;
    text-align: center;
    color: var(--text-grey);
    font-size: 16px;
    line-height: 20px;
  }
  .advisor-name {
    color: var(--ink-blue);
    font-size: 20px;
    font-weight: 600;
    line-height: 26px;
  }
  .advisor-name .credentials { font-size: 15px; }
  .advisor-role { margin-top: 1px; }
  .address { margin-top: 16px; }
  .reach { margin-top: 20px; }
  .reach-line { display: flex; justify-content: center; align-items: center; gap: 7px; }
  .reach-line svg { fill: var(--ink-blue); flex: none; }
  .fax-line {
    margin-top: 6px;
    color: var(--ink-blue);
    font-weight: 700;
    font-size: 16px;
  }

  .card-back .brand-name {
    top: 252px;
    color: var(--card-white);
    font-size: 24px;
    line-height: 1.25;
  }
  .tagline {
    position: absolute;
    top: 358px;
    left: 0; right: 0;
    text-align: center;
    color: var(--card-white);
    font-weight: 700;
    font-size: 16px;
    line-height: 20px;
  }
</style>
</head>
<body>
  <section class="card card-front" aria-label="Business card front">
    <div class="accent-tab accent-tab-top"></div>

    <div class="brand-name">Harborview Nest Advisors, LLC</div>
    <div class="brand-rule"></div>

    <div class="contact">
      <div class="advisor-name">Gregor Pelham, <span class="credentials">MBA, ChFC®, CLU®</span></div>
      <div class="advisor-role">Financial Advisor<br>Registered Representative</div>

      <div class="address">2187 Meadowlark Ridge Rd.<br>Suite K418<br>Virginia Beach, VA 23999</div>

      <div class="reach">
        <div class="reach-line">
          <svg width="11" height="11" viewBox="0 0 24 24" aria-hidden="true"><path d="M6.6 10.8a15.1 15.1 0 0 0 6.6 6.6l2.2-2.2a1 1 0 0 1 1-.25 11.4 11.4 0 0 0 3.6.57 1 1 0 0 1 1 1V20a1 1 0 0 1-1 1A17 17 0 0 1 3 4a1 1 0 0 1 1-1h3.5a1 1 0 0 1 1 1c0 1.25.2 2.45.57 3.57a1 1 0 0 1-.25 1z"/></svg>
          <span>(555) 318-2946</span>
        </div>
        <div class="reach-line">
          <svg width="10" height="8" viewBox="0 0 20 16" aria-hidden="true"><path d="M0 0h20v2l-10 6L0 2z M0 4l10 6 10-6v12H0z"/></svg>
          <span>gpelham@harborviewnest.example</span>
        </div>
      </div>
      <div class="fax-line">Toll Free Fax: (800) 555-0193</div>
    </div>

    <div class="accent-tab accent-tab-bottom"></div>
  </section>

  <section class="card card-back" aria-label="Business card back">
    <div class="brand-name">Harborview Nest Advisors, LLC</div>
    <div class="tagline">Turning Your Earned Income Into<br>Retirement Income</div>
  </section>
</body>
</html>
```